Modern business card design for professional copywriter

I'd like a business card design that I can use to have my cards printed out by quillprint.com as a squared corners business card (see artwork and design guidelines here: https://help.quillprint.com/hc/en-gb/sections/200570950-QUILL-Product-Templates)

The design should be clean and modern and reflect the colours, tone and branding on my website: https://tessavorrin.com.au

Target Market(s)

Professionals, B2B small business owners

Industry/Entity Type

Business

Contact Information for Business Card

Tessa Vorrin
m: 0468 905 327
e: tessa@tessavorrin.com.au
w: tessavorrin.com.au

Font styles to use
Sans Serif

Requirements
Must have
• Tagline: "Smart copywriting for clever business people"
• Brand colours: fd8000, 009984, 666666 and black
Nice to have

```html
<!DOCTYPE html>
<html lang="en">
<head>
<meta charset="UTF-8">
<title>Tessa Vorrin – Business Card</title>
<link href="https://fonts.googleapis.com/css2?family=Jost:wght@400;500&display=swap" rel="stylesheet">
<style>
  :root {
    --orange: #fd8000;
    --teal: #009984;
    --grey: #666666;
    --ink: #333333;
    --card: #ffffff;
    --backdrop: #e9e6e1;
  }
  * { margin: 0; padding: 0; box-sizing: border-box; }
  html, body { width: 1200px; height: 1000px; overflow: hidden; }
  body {
    background: var(--backdrop);
    font-family: "Jost", "Futura", sans-serif;
    position: relative;
  }
  .card {
    position: absolute;
    left: 295px;
    width: 587px;
    height: 334px;
    background: var(--card);
    box-shadow: 0 6px 14px rgba(0,0,0,0.18);
  }
  .card--front { top: 150px; }
  .card--back { top: 517px; }

  .brand-mark {
    position: absolute;
    display: flex;
    align-items: center;
    gap: 10px;
    color: var(--teal);
    font-weight: 500;
    white-space: nowrap;
  }
  .brand-mark__square {
    display: block;
    background: var(--orange);
  }
  .card--front .brand-mark { left: 36px; top: 152px; font-size: 34px; }
  .card--front .brand-mark__square { width: 16px; height: 16px; }
  .card--back .brand-mark { left: 50%; top: 150px; transform: translateX(-50%); font-size: 44px; }
  .card--back .brand-mark__square { width: 20px; height: 20px; }

  .rule {
    position: absolute;
    left: 322px;
    width: 3px;
    background: var(--teal);
  }
  .rule--name { top: 112px; height: 40px; }
  .rule--contact { top: 172px; height: 54px; }

  .identity { position: absolute; left: 342px; top: 110px; line-height: 21px; }
  .identity__name { color: var(--orange); font-size: 18px; }
  .identity__role { color: var(--ink); font-size: 16px; }

  .contact { position: absolute; left: 346px; top: 170px; list-style: none; }
  .contact__item {
    display: flex;
    align-items: center;
    gap: 10px;
    height: 20px;
    font-size: 14px;
    color: var(--ink);
    letter-spacing: 0.3px;
  }
  .contact__icon { width: 10px; height: 10px; flex: none; }

  .tagline {
    position: absolute;
    left: 0; right: 0;
    top: 288px;
    text-align: center;
    font-size: 14px;
    color: #444;
    letter-spacing: 0.6px;
  }
</style>
</head>
<body>
  <section class="card card--front">
    <div class="brand-mark"><span class="brand-mark__square"></span>Tessa Vorrin</div>

    <span class="rule rule--name"></span>
    <div class="identity">
      <div class="identity__name">Tessa Vorrin</div>
      <div class="identity__role">Copywriter</div>
    </div>

    <span class="rule rule--contact"></span>
    <ul class="contact">
      <li class="contact__item">
        <svg class="contact__icon" viewBox="0 0 10 10"><rect x="2.5" y="0.5" width="5" height="9" rx="1" fill="none" stroke="#fd8000" stroke-width="1.2"/><circle cx="5" cy="8" r="0.6" fill="#fd8000"/></svg>
        0468 905 327
      </li>
      <li class="contact__item">
        <svg class="contact__icon" viewBox="0 0 10 10"><rect x="0.5" y="2" width="9" height="6.5" fill="#fd8000"/><path d="M0.5 2 L5 5.6 L9.5 2" fill="none" stroke="#fff" stroke-width="0.9"/></svg>
        tessa@tessavorrin.com.au
      </li>
      <li class="contact__item">
        <svg class="contact__icon" viewBox="0 0 10 10"><circle cx="4" cy="4" r="3" fill="none" stroke="#fd8000" stroke-width="1.5"/><path d="M6.2 6.2 L9.3 9.3" stroke="#fd8000" stroke-width="1.8" stroke-linecap="round"/></svg>
        tessavorrin.com.au
      </li>
    </ul>
  </section>

  <section class="card card--back">
    <div class="brand-mark"><span class="brand-mark__square"></span>Tessa Vorrin</div>
    <p class="tagline">Smart copywriting for clever business people</p>
  </section>
</body>
</html>
```